Lotstallmart.com Webpage Design

Design Brief for lotstallmart.com (Copy of Brief also in attached Word file)

Name of Website- lotstallmart.com (existing logo and look & feel of website to be changed)

Logo - Finalised. The logo files are attached with the brief as “logo.jpeg”. The “Blue- Grey” version of the logo is for use on lighter backgrounds and the “Orange-White” version of the logo is for use on darker backgrounds. (A full Black version of the logo is also attached). Both versions may be used in different parts of the website. All attached files are in .png format.
Status - The website in functional and is undergoing user trials. However, we want to improve the look & feel of the website so at it seems
a. cotemporary,
b. Easy to Navigate
c. professional and
d. Vibrant.

Please visit ‘lotstallmart.com’ to check out the website and its functionalities – please use it only as a reference for the features & functions to be provided, however the designer should use a ‘Free Hand’ in designing the composition of various parts of the webpage without getting too influenced by the existing design

Objective of the Website ‘lotstallmart.com –
a. It is a portal focussed on listing of ‘Retail’ specific real-estate properties by developers, owners and realty brokers. The properties shall listed under the following four categories-
i. Retail Malls
ii. Shopping Complexes
iii. High-street shops
iv. Retail Warehouses
*refer lotstallmart.com for better clarity

b. The abovementioned properties shall be listed either for ‘Sale’ or ‘rent\lease’ or both

c. Users shall visit the site in case they wish to acquire a retail \ shop space either on ‘sale’ or ‘rent’. These Users would be able to specify the ‘Search Criteria’ through the tool-bars provided on the website – the ‘Search Criteria’ shall comprise of ‘Type of space category’, ‘City’, ‘Locality’, transaction type ie ‘Rent \ Sale’ and ‘Area Range’

d. The main revenue model for the website shall be listing fee ( or advertising charges ) payable by those listing their properties on the website.

Three Main Pages of Website (lotstallmart.com) that need to be designed -
a. Main Home Page (visit the web link - http://lotstallmart.com/ ) - The main home page has the “Search Toolbar” for specifying of Search Criteria by the User. It shall also have the following features & functions-
i. Main Advertising Banner
ii. Featured Projects
iii. New Launches
iv. Toolbar with buttons – ‘Advertise with Us’, ‘Listings Alert’, ‘Mart Wizards’, ‘Advertiser Login’

b. Property Listings Page (visit the web link - http://lotstallmart.com/gurgaon-in-india ) - The List of property options that match the Criteria specified by the ‘User’ get displayed on this page.

c. Property Detail Page - When the ‘User’ clicks on the “More….” Button on the ‘Property Listings Page’ (given in point b. above) the web page with the details of the property opens. (For Example – visit the web link - http://lotstallmart.com/vorne-Shopping-Complex-vorne-quadrion-gurgaon-636 )

Note:- Please refer to attached ‘Shopping’ related images the designer may use them on the website to provide a look & feel of retail if required – either separately or rotate in a single window

Target Market(s)

Retailers & Investors looking for retail space, Real Estate Brokers, Developers

Industry/Entity Type

Advertising

Number of Pages Required

3 page

Requirements
Must have
• Refer to existing site lotstallmart.com -- all the existing functionalities are a must have.
Nice to have
• The Designer may use the retail related images on the website if required for making it more vibrant. Refer attached images Shopping(1-6).jpg

```html
<!DOCTYPE html>
<html lang="en">
<head>
<meta charset="utf-8">
<title>Lotstallmart.com – Retail Space Portal</title>
<link href="https://fonts.googleapis.com/css2?family=Open+Sans:wght@400;600;700&display=swap" rel="stylesheet">
<style>
:root{
  --blue:#1b88f1;
  --blue-dark:#1570cc;
  --ink:#333;
  --muted:#666;
  --topbar:#3b3b3b;
  --footer:#2c2f36;
  --footer-deep:#24272d;
  --page:#f4f4f4;
  --card:#fff;
  --btn:#2f2f2f;
}
*{margin:0;padding:0;box-sizing:border-box}
html,body{width:1200px;height:2528px;overflow:hidden}
body{position:relative;background:var(--page);font-family:"Open Sans",Arial,sans-serif;color:var(--ink)}
.abs{position:absolute}

/* city bar */
.city-bar{left:0;top:0;width:1200px;height:37px;background:var(--topbar);display:flex;align-items:center;padding-left:104px;font-size:12.5px;color:#d6d6d6;white-space:nowrap}
.city-bar span{padding:0 17px;border-right:1px solid #777;line-height:13px}
.city-bar span:first-child{padding-left:0}
.city-bar span:last-child{border-right:0}

/* header */
.site-header{left:0;top:37px;width:1200px;height:98px;background:#f7f7f7}
.brand{left:100px;top:24px;display:flex;align-items:center;gap:10px;font-size:28px;font-weight:700;color:var(--blue-dark);white-space:nowrap}
.brand-dot{width:30px;height:30px;border-radius:50%;background:var(--blue-dark)}
.main-nav{left:514px;top:39px;display:flex;font-size:13px;color:#444;white-space:nowrap}
.main-nav a{text-decoration:none;color:inherit;margin-right:46px}
.main-nav a.active{color:var(--blue)}
.login-btn{left:972px;top:29px;width:128px;height:44px;background:var(--blue);color:#fff;font-size:13px;display:flex;align-items:center;justify-content:center;border-radius:2px;white-space:nowrap}

/* hero */
.hero{left:0;top:135px;width:1200px;height:633px;background:
  radial-gradient(ellipse at 70% 40%,rgba(240,210,120,.55),transparent 45%),
  radial-gradient(ellipse at 30% 60%,rgba(60,150,170,.5),transparent 40%),
  linear-gradient(100deg,#3a2a22 0%,#6b4b36 35%,#a57b4a 55%,#4a2f24 80%,#2a1e1a 100%)}
.hero-title{left:98px;top:359px;height:62px;background:rgba(40,40,40,.8);color:#fff;font-size:33px;font-weight:600;display:flex;align-items:center;padding:0 20px;white-space:nowrap}
.hero-sub{left:98px;top:435px;width:475px;height:54px;background:rgba(40,40,40,.55);color:#eee;font-size:17px;display:flex;align-items:center;padding-left:20px;white-space:nowrap}
.hero-arrow{top:428px}
.hero-arrow.prev{left:18px}
.hero-arrow.next{left:1132px}

/* search */
.space-tabs{left:98px;top:672px;width:605px;height:44px;background:#fff;font-size:12px;color:#444;white-space:nowrap}
.space-tabs label{position:absolute;top:13px;display:flex;align-items:center}
.space-tabs i{width:17px;height:17px;border:1px solid #999;margin-right:10px;display:inline-block;flex-shrink:0}
.search-bar{left:98px;top:716px;width:1002px;height:108px;background:var(--blue);box-shadow:0 14px 18px -12px rgba(0,0,0,.35)}
.search-title{left:16px;top:41px;color:#fff;font-size:18px;font-weight:600}
.field{position:absolute;top:22px}
.field label{display:block;color:#fff;font-size:12px;margin-bottom:8px;white-space:nowrap}
.field .box{height:34px;background:#fff;border:1px solid #ccc;position:relative;font-size:10px;color:#555;padding:11px 8px;white-space:nowrap}
.field .box.select::after{content:"";position:absolute;right:3px;top:9px;width:12px;height:14px;background:#ddd;border:1px solid #999}
.search-go{right:0;top:0;width:145px;height:108px;background:#3a3a3a;clip-path:polygon(16% 0,100% 0,100% 100%,0 100%);color:#fff;font-size:15px;font-weight:600;text-align:center;padding:34px 0 0 20px;line-height:22px;white-space:nowrap}

/* sections */
.section-title{font-size:21px;font-weight:400;color:#333;white-space:nowrap}
.section-title b{font-weight:400;color:#1f78c8}
.view-all{font-size:12px;font-style:italic;color:var(--blue);display:flex;align-items:center;white-space:nowrap}
.view-all .pager{width:20px;height:20px;background:#777;margin-left:4px;display:flex;align-items:center;justify-content:center}

.card{width:317px;height:372px;background:var(--card);box-shadow:0 1px 3px rgba(0,0,0,.15);text-align:center}
.card .photo{position:absolute;left:12px;top:10px;width:293px;height:229px}
.card .place{position:absolute;right:0;bottom:0;background:rgba(40,40,40,.65);color:#fff;font-size:15px;padding:10px 18px}
.card h3{position:absolute;left:0;right:0;top:255px;font-size:16px;font-weight:400;color:#333;white-space:nowrap}
.card .type{position:absolute;left:0;right:0;top:289px;font-size:12px;font-weight:600;color:var(--blue)}
.card .btn{position:absolute;left:84px;top:315px;width:126px;height:41px;background:var(--btn);color:#fff;font-size:12.5px;display:flex;align-items:center;justify-content:center;border-radius:3px;white-space:nowrap}

.categories{left:98px;top:1353px;width:1002px;height:256px;background:#fff;box-shadow:0 14px 18px -14px rgba(0,0,0,.3)}
.cat{position:absolute;top:0;width:220px;text-align:center}
.cat svg{margin-top:37px}
.cat h4{font-size:15px;font-weight:400;color:#333;margin-top:14px;white-space:nowrap}
.cat p{font-size:12.5px;color:#555;line-height:19px;margin-top:12px;white-space:nowrap}

/* newsletter + footer */
.site-footer{left:0;top:2196px;width:1200px;height:332px;background:var(--footer);color:#aaa;font-size:11px}
.newsletter{left:98px;top:2153px;width:1002px;height:81px;background:var(--blue);display:flex;align-items:center}
.newsletter h2{font-size:21px;font-weight:400;color:#fff;margin-left:22px;width:335px;white-space:nowrap}
.newsletter .input{width:231px;height:42px;background:#fff;font-size:11px;color:#888;padding:14px 12px;margin-right:13px}
.newsletter .signup{width:111px;height:42px;background:#3a3a3a;color:#fff;font-size:13px;font-weight:600;display:flex;align-items:center;justify-content:center}
.foot-col h5{font-size:15px;font-weight:400;color:#fff;margin-bottom:20px;white-space:nowrap}
.foot-col ul{list-style:none;line-height:24px;white-space:nowrap}
.foot-about p{line-height:19px;color:#bbb;width:376px}
.foot-about .more{color:var(--blue);margin-top:6px}
.foot-contact p{line-height:19px;color:#bbb;white-space:nowrap}
.foot-bottom{left:0;top:2463px;width:1200px;height:65px;background:var(--footer-deep)}
.copyright{left:98px;top:24px;font-size:11px;color:#888;white-space:nowrap}
.social{left:933px;top:14px;display:flex;gap:12px}
.social i{width:34px;height:34px;border-radius:50%;border:2px solid #fff;display:block}
</style>
</head>
<body>

<nav class="abs city-bar">
  <span>Bangalore</span><span>Chennai</span><span>Greater Noida</span><span>Gurgaon</span><span>Hyderabad</span><span>Jaipur</span><span>Khanna</span><span>Kolkatta</span><span>Mumbai</span><span>Noida</span><span>Pune</span><span>Surat</span>
</nav>

<header class="abs site-header">
  <div class="abs brand"><span class="brand-dot"></span>lotstallmart.com</div>
  <nav class="abs main-nav">
    <a class="active">Home</a><a>Advertise with Us</a><a>Listings Alert</a><a>Mart Wizards</a>
  </nav>
  <div class="abs login-btn">Advertiser Login</div>
</header>

<section class="abs hero" role="img" aria-label="Banner photo of smiling shoppers with colourful shopping bags on a mall escalator"></section>
<div class="abs hero-title">Grand Arcade Gurgaon</div>
<div class="abs hero-sub">Lorem ipsum dolor sit amet, consectetuer adipiscing eli</div>
<svg class="abs hero-arrow prev" width="50" height="50" viewBox="0 0 50 50"><circle cx="25" cy="25" r="22" fill="rgba(0,0,0,.25)" stroke="#ddd" stroke-width="3"/><path d="M29 15 L19 25 L29 35" fill="none" stroke="#ddd" stroke-width="4"/></svg>
<svg class="abs hero-arrow next" width="50" height="50" viewBox="0 0 50 50"><circle cx="25" cy="25" r="22" fill="rgba(0,0,0,.25)" stroke="#ddd" stroke-width="3"/><path d="M21 15 L31 25 L21 35" fill="none" stroke="#ddd" stroke-width="4"/></svg>

<div class="abs space-tabs">
  <label style="left:15px"><i></i>Retail Malls</label>
  <label style="left:131px"><i></i>Shopping Complexes</label>
  <label style="left:302px"><i></i>High-street shops</label>
  <label style="left:448px"><i></i>Retail&nbsp; Warehouses</label>
</div>
<form class="abs search-bar">
  <div class="abs search-title">Search</div>
  <div class="field" style="left:106px;width:175px"><label>Type of space category</label><div class="box select"></div></div>
  <div class="field" style="left:298px;width:88px"><label>City</label><div class="box select"></div></div>
  <div class="field" style="left:401px;width:126px"><label>Locality</label><div class="box select"></div></div>
  <div class="field" style="left:542px;width:128px"><label>Transaction type</label><div class="box">Rent \ Sale</div></div>
  <div class="field" style="left:684px;width:128px"><label>Area Range</label><div class="box select"></div></div>
  <div class="abs search-go">SEARCH<br>LAND SPACE</div>
</form>

<h2 class="abs section-title" style="left:98px;top:870px">Featured <b>Retail</b> Projects</h2>
<div class="abs view-all" style="left:1006px;top:885px">View all&nbsp;&nbsp;<span class="pager"><svg width="8" height="10"><path d="M7 0 L1 5 L7 10Z" fill="#fff"/></svg></span><span class="pager"><svg width="8" height="10"><path d="M1 0 L7 5 L1 10Z" fill="#fff"/></svg></span></div>

<article class="abs card" style="left:98px;top:930px">
  <div class="photo" role="img" aria-label="Family shopping in a mall with a sale sign" style="background:linear-gradient(135deg,#6b5a44,#c9a64a 45%,#3d3a3a)"><span class="place">Faridabad</span></div>
  <h3>Vestra 81 High StreetSector-81</h3><div class="type">Shopping Complex</div><div class="btn">View the listing</div>
</article>
<article class="abs card" style="left:441px;top:930px">
  <div class="photo" role="img" aria-label="City skyline of tall office towers" style="background:linear-gradient(180deg,#6f8fb3,#9aabbd 45%,#4d5560)"><span class="place">Faridabad</span></div>
  <h3>Vestra 81 High StreetSector-81</h3><div class="type">Shopping Complex</div><div class="btn">View the listing</div>
</article>
<article class="abs card" style="left:784px;top:930px">
  <div class="photo" role="img" aria-label="Night city street with colourful light trails" style="background:linear-gradient(160deg,#1a1838,#6a2f8a 45%,#d84a6a 70%,#2a6fb5)"><span class="place">Faridabad</span></div>
  <h3>Vestra 81 High StreetSector-81</h3><div class="type">Shopping Complex</div><div class="btn">View the listing</div>
</article>

<section class="abs categories">
  <div class="cat" style="left:8px">
    <svg width="90" height="90" viewBox="0 0 90 90"><circle cx="45" cy="45" r="43" fill="#fff" stroke="#333" stroke-width="3"/><g fill="var(--blue)"><rect x="24" y="36" width="10" height="26"/><rect x="36" y="26" width="12" height="36"/><rect x="50" y="32" width="10" height="30"/><rect x="62" y="42" width="6" height="20"/></g></svg>
    <h4>Retail Malls</h4><p>In pharetra dui vitae odio maximus<br>vulputate. Nul am finibus dui.</p>
  </div>
  <div class="cat" style="left:265px">
    <svg width="90" height="90" viewBox="0 0 90 90"><circle cx="45" cy="45" r="43" fill="#fff" stroke="#333" stroke-width="3"/><g fill="var(--blue)"><rect x="26" y="48" width="8" height="16"/><rect x="37" y="40" width="8" height="24"/><rect x="48" y="32" width="8" height="32"/><rect x="59" y="24" width="8" height="40"/></g></svg>
    <h4>Shopping Complexes</h4><p>In pharetra dui vitae odio maximus<br>vulputate. Nul am finibus dui.</p>
  </div>
  <div class="cat" style="left:508px">
    <svg width="90" height="90" viewBox="0 0 90 90"><circle cx="45" cy="45" r="43" fill="#fff" stroke="#333" stroke-width="3"/><g fill="var(--blue)"><rect x="36" y="22" width="18" height="44"/><rect x="42" y="16" width="6" height="6"/></g></svg>
    <h4>High-street shops</h4><p>In pharetra dui vitae odio maximus<br>vulputate. Nul am finibus dui.</p>
  </div>
  <div class="cat" style="left:764px">
    <svg width="90" height="90" viewBox="0 0 90 90"><circle cx="45" cy="45" r="43" fill="#fff" stroke="#333" stroke-width="3"/><g fill="var(--blue)"><path d="M24 40 L45 24 L66 40Z"/><rect x="28" y="42" width="34" height="22"/></g><rect x="40" y="50" width="10" height="14" fill="#fff"/></svg>
    <h4>Retail&nbsp; Warehouses</h4><p>In pharetra dui vitae odio maximus<br>vulputate. Nul am finibus dui.</p>
  </div>
</section>

<h2 class="abs section-title" style="left:98px;top:1667px">Featured <b>New</b> Launches</h2>
<div class="abs view-all" style="left:1006px;top:1682px">View all&nbsp;&nbsp;<span class="pager"><svg width="8" height="10"><path d="M7 0 L1 5 L7 10Z" fill="#fff"/></svg></span><span class="pager"><svg width="8" height="10"><path d="M1 0 L7 5 L1 10Z" fill="#fff"/></svg></span></div>

<article class="abs card" style="left:98px;top:1727px">
  <div class="photo" role="img" aria-label="Glass skyscrapers under a teal sky" style="background:linear-gradient(180deg,#7fb3a8,#3f6b6a 50%,#1f2e33)"><span class="place">Faridabad</span></div>
  <h3>Vestra 81 High StreetSector-81</h3><div class="type">Shopping Complex</div><div class="btn">View the listing</div>
</article>
<article class="abs card" style="left:441px;top:1727px">
  <div class="photo" role="img" aria-label="Shoppers walking through an outdoor shopping street" style="background:linear-gradient(180deg,#4a3a2c,#8a6a4a 50%,#5a4a40)"><span class="place">Faridabad</span></div>
  <h3>Vestra 81 High StreetSector-81</h3><div class="type">Shopping Complex</div><div class="btn">View the listing</div>
</article>
<article class="abs card" style="left:784px;top:1727px">
  <div class="photo" role="img" aria-label="Downtown office buildings against a blue sky" style="background:linear-gradient(180deg,#6f9ed4,#b7c4d0 45%,#8a6a55)"><span class="place">Faridabad</span></div>
  <h3>Vestra 81 High StreetSector-81</h3><div class="type">Shopping Complex</div><div class="btn">View the listing</div>
</article>

<footer class="abs site-footer">
  <div class="abs foot-col" style="left:98px;top:78px">
    <h5>About Retail Hub</h5>
    <ul class="abs" style="left:0;top:40px;width:90px"><li>About Us</li><li>Privacy Policy</li><li>Terms of Use</li><li>Contact Us</li><li>Site Map</li></ul>
    <ul class="abs" style="left:106px;top:40px;width:130px"><li>Retail Malls</li><li>Shopping Complex</li><li>High Street Shops</li><li>Retail Warehouses</li></ul>
  </div>
  <div class="abs foot-col foot-about" style="left:441px;top:78px">
    <h5>www.lotstallmart.com</h5>
    <p>Lotstallmart.com - About Us Lotstallmart.com is a Specialised Web based platform for Retail Space, featuring properties across India under various formats such as Retail Malls, Shopping Complexes, High-street Shops. Also featured are "Retail Warehouses"</p>
    <p class="more">Read More</p>
  </div>
  <div class="abs foot-col foot-contact" style="left:955px;top:78px">
    <h5>Contact</h5>
    <p>&nbsp;Retail Hub<br>Unit 512, 5th Floor,<br>Lorem ipsum is simply,<br>Sector-x, Gurgaon - 122002<br>&nbsp;Phone : 000-000-0000<br>Fax : 000 - 000 - 0000</p>
  </div>
</footer>

<div class="abs newsletter">
  <h2>Subscribe Newsletter Sign Up</h2>
  <div class="input">Name:</div>
  <div class="input">Email Address:</div>
  <div class="signup">SIGN UP</div>
</div>

<div class="abs foot-bottom">
  <div class="abs copyright">Copyright © 2015 Retail Hub India.com. All rights reserved.</div>
  <div class="abs social">
    <i style="background:#3b5a9a"></i><i style="background:#2aa3e0"></i><i style="background:#1f6fa8"></i><i style="background:#e07a1a"></i>
  </div>
</div>

</body>
</html>
```